i need a business card design for my family investment company "quorin investments" based in dubai. its a diverse investment firm focusing on education, hospitality and automotive. the design has to be modern and try to incorporate the logo "E" in the design. details on card as follow

Yusuf K Bin Tarrah
Managing Director
yusuf@quorin-mail.ae
www.quorin-mail.ae

Harbor district,palwick tower, office 2212, dubai
tel. 04 3850927
mobile.050 9184203

card used for networking events and investor meetings

Hospitality

```html
<!DOCTYPE html>
<html lang="en">
<head>
<meta charset="utf-8">
<title>Quorin Investments – Business Card</title>
<link rel="stylesheet" href="https://fonts.googleapis.com/css2?family=Lato:wght@300;400;700&display=swap">
<style>
  :root {
    --page-bg: #e9e7e3;
    --card-white: #ffffff;
    --ink: #3a3d42;
    --ink-soft: #55595f;
    --accent: #5b8db5;
    --rule: #3f4247;
    --blue-deep: #3e6d94;
    --blue-light: #86bdd6;
    --on-blue: #eef6fa;
    --shadow: rgba(0, 0, 0, 0.22);
  }
  * { box-sizing: border-box; margin: 0; padding: 0; }
  html, body {
    width: 1200px; height: 1023px; overflow: hidden;
    background: var(--page-bg);
    font-family: "Lato", Arial, sans-serif;
  }
  .canvas { position: relative; width: 1200px; height: 1023px; }

  .card {
    position: absolute;
    width: 620px; height: 354px;
    border-radius: 3px;
    box-shadow: 0 10px 28px var(--shadow);
  }

  /* Front */
  .card-front { left: 70px; top: 80px; background: var(--card-white); color: var(--ink); }
  .card-front .wordmark {
    position: absolute; left: 0; right: 0; top: 52px;
    text-align: center;
  }
  .wordmark-name {
    font-weight: 300; font-size: 34px; letter-spacing: 12px;
    text-transform: uppercase; color: var(--ink);
  }
  .wordmark-sub {
    display: block; margin-top: 4px;
    font-weight: 300; font-size: 12px; letter-spacing: 9px;
    text-transform: uppercase; color: var(--ink);
  }
  .card-front .divider {
    position: absolute; left: 160px; right: 36px; top: 196px;
    height: 1px; background: var(--rule);
  }
  .holder { position: absolute; left: 36px; top: 158px; }
  .holder-name { font-weight: 700; font-size: 17px; color: var(--accent); }
  .holder-title { font-size: 13px; color: var(--ink-soft); margin-top: 2px; }

  .contact-list { position: absolute; left: 36px; top: 232px; list-style: none; }
  .contact-list li {
    display: flex; align-items: center; gap: 10px;
    font-size: 13px; line-height: 20px; color: var(--ink-soft);
  }
  .contact-list svg { width: 12px; height: 12px; flex: none; }

  .office { position: absolute; right: 36px; top: 118px; text-align: right; }
  .office-name { font-weight: 700; font-size: 14px; color: var(--accent); }
  .office-line { font-size: 13px; line-height: 19px; color: var(--ink-soft); }

  /* Back */
  .card-back {
    left: 510px; top: 600px;
    background: linear-gradient(115deg, var(--blue-deep) 0%, var(--blue-light) 55%, var(--blue-deep) 100%);
    color: var(--on-blue);
  }
  .card-back .wordmark { position: absolute; left: 0; right: 0; top: 120px; text-align: center; }
  .card-back .wordmark-name, .card-back .wordmark-sub { color: var(--on-blue); }
  .card-back .wordmark-name { font-size: 40px; letter-spacing: 14px; }
  .card-back .web {
    position: absolute; left: 0; right: 0; bottom: 34px; text-align: center;
    font-size: 14px; letter-spacing: 1px; color: var(--on-blue);
  }
</style>
</head>
<body>
<main class="canvas">

  <section class="card card-front" aria-label="Business card front">
    <div class="wordmark">
      <span class="wordmark-name">Quorin</span>
      <span class="wordmark-sub">Investments</span>
    </div>

    <div class="holder">
      <p class="holder-name">Yusuf K Bin Tarrah</p>
      <p class="holder-title">Managing Director</p>
    </div>

    <div class="divider"></div>

    <div class="office">
      <p class="office-name">Quorin Investments</p>
      <p class="office-line">Harbor district, palwick tower</p>
      <p class="office-line">Office 2212, Dubai</p>
    </div>

    <ul class="contact-list">
      <li>
        <svg viewBox="0 0 12 12"><path d="M3 1 L5 3.5 L4 5 Q5.5 7 7 8 L8.5 7 L11 9 L10 11 Q4 11 1 2 Z" fill="var(--accent)"/></svg>
        04 3850927
      </li>
      <li>
        <svg viewBox="0 0 12 12"><rect x="3" y="0.5" width="6" height="11" rx="1" fill="none" stroke="var(--accent)" stroke-width="1.2"/></svg>
        050 9184203
      </li>
      <li>
        <svg viewBox="0 0 12 12"><rect x="0.6" y="2" width="10.8" height="8" fill="none" stroke="var(--accent)" stroke-width="1.2"/><path d="M0.6 2 L6 6.5 L11.4 2" fill="none" stroke="var(--accent)" stroke-width="1.2"/></svg>
        yusuf@quorin-mail.ae
      </li>
      <li>
        <svg viewBox="0 0 12 12"><circle cx="6" cy="6" r="5" fill="none" stroke="var(--accent)" stroke-width="1.2"/><path d="M1 6 H11 M6 1 Q3 6 6 11 Q9 6 6 1" fill="none" stroke="var(--accent)" stroke-width="1"/></svg>
        www.quorin-mail.ae
      </li>
    </ul>
  </section>

  <section class="card card-back" aria-label="Business card back">
    <div class="wordmark">
      <span class="wordmark-name">Quorin</span>
      <span class="wordmark-sub">Investments</span>
    </div>
    <p class="web">www.quorin-mail.ae</p>
  </section>

</main>
</body>
</html>
```